Web Design Project

We are an IT System Integrator. We provide Korvin 450 ERP System, CRM etc. We also provide hardware, networking servicing. Please look at www.zolvantix.com.sg. They provide the same service as us. We like to redesign our web site. I will attached the color that I prefer for reference.

Our website is www.tadurk.com.sg.  It has been created about 14 years ago.  We are trying to revamp it with a new look and information.   The new website must be informative, fast.    I have attached an attachment which show the color that I prefer(brownish golden).   

Our competitor (www.zolvantix.com) is carrying the same trade as us.  They have all the informations In their website that we will like to have.  Therefore I recommend you to take a look at my competitor website and have a better   
understanding on the kind of information I would like to have for my new website.

This project is guarantee to the person with the best design.  We can have it guarantee.

Target Market(s)

Corporate and companies

Industry/Entity Type

Hardware

```html
<!DOCTYPE html>
<html lang="en">
<head>
<meta charset="utf-8">
<title>Tadurk Information Systems</title>
<link rel="stylesheet" href="https://fonts.googleapis.com/css2?family=Ubuntu:wght@400;500&family=Open+Sans:wght@300;400&family=Noto+Sans&family=Arimo:ital@0;1&display=swap">
<style>
:root{
  --brown:#b07535;
  --brown-dark:#8f5c27;
  --gold:#c08a3a;
  --page:#ececec;
  --panel:#f6f6f7;
  --line:#d9d9d9;
  --ink:#333;
  --muted:#777;
  --white:#fff;
}
*{margin:0;padding:0;box-sizing:border-box}
html,body{width:1046px;height:1200px;overflow:hidden}
body{background:var(--page);font-family:"Arimo",Arial,sans-serif;color:var(--ink);position:relative}
.abs{position:absolute}
.header{left:0;top:0;width:1046px;height:124px;background:linear-gradient(#f6f6f6,#ebebeb)}
.logo-art{left:122px;top:20px;width:120px;height:85px;border-radius:8px;background:radial-gradient(circle at 50% 45%,#e4b665,#b98335 60%,#ececec 100%)}
.logo-name{left:249px;top:34px;font-family:"Ubuntu",sans-serif;font-weight:500;font-size:11.5px;line-height:23px;color:var(--gold);letter-spacing:.3px}
.top-links{left:440px;top:18px;font-size:9px;color:#888;letter-spacing:.2px;display:flex;gap:14px}
.top-links span.sep{color:#aaa}
.main-nav{left:0;top:124px;width:1046px;height:26px;background:var(--brown)}
.main-nav .item{position:absolute;top:7px;font-family:"Ubuntu",sans-serif;font-weight:500;font-size:10.5px;color:var(--white)}
.main-nav .active{top:-6px;left:286px;width:67px;height:32px;background:linear-gradient(#d9d9d9,#f2f2f2 30%);border-radius:3px 3px 0 0;color:var(--brown);text-align:center;padding-top:12px}
.hero-art{left:142px;top:158px;width:337px;height:288px;border-radius:40%;background:radial-gradient(ellipse at 50% 45%,#e1e1e1,#ececec 70%)}
.hero-text{left:463px;top:210px;width:420px;font-family:"Open Sans",sans-serif;font-weight:300;font-size:20px;line-height:36.5px;color:#2c2c2c}
.hero-text em{font-style:normal;color:var(--gold)}
.arrow{width:27px;height:27px}
.dots span{position:absolute;top:460px;width:30px;height:7px;border-radius:4px;background:#fafafa;box-shadow:0 1px 2px rgba(0,0,0,.3)}
.dots span.on{background:#c49a5a}
.card{top:488px;height:176px;width:234px;background:var(--panel);border:1px solid #dedede}
.card h2{position:absolute;left:23px;top:8px;font-family:"Ubuntu",sans-serif;font-weight:500;font-size:18px;color:var(--brown)}
.card .rule{position:absolute;left:15px;right:15px;top:39px;border-top:1px solid #cfcfcf}
.card p{position:absolute;left:17px;top:50px;width:205px;font-size:10.3px;line-height:17px;color:#333}
.card p.about{width:200px}
.card p.quote{left:31px;font-style:italic;width:172px;line-height:14.7px;top:54px;font-size:10px}
.card .qmark{position:absolute;left:17px;top:51px;font-size:14px;color:#999;font-family:Georgia,serif}
.card .by{position:absolute;left:158px;top:135px;font-size:9.5px;color:var(--brown)}
.btn{position:absolute;height:19px;padding:0 7px;background:var(--brown);color:var(--white);font-size:9.5px;line-height:19px;border-radius:2px}
.mascot{width:40px;height:61px;border-radius:6px;background:linear-gradient(#d9a658,#a87234)}
.form label{position:absolute;left:14px;font-size:10.5px;color:#222}
.form .field{position:absolute;left:65px;width:154px;height:15px;background:linear-gradient(#dcdde0,#eeeff1);border:1px solid #e3e3e3}
.panel{top:691px;height:335px;background:var(--panel);border:1px solid #dedede}
.tab{top:683px;height:29px;background:linear-gradient(var(--brown),#a56c2f);border-radius:6px 6px 0 0;font-family:"Ubuntu",sans-serif;font-weight:500;font-size:17.5px;color:var(--white);text-align:center;line-height:31px;box-shadow:inset 0 -3px 0 rgba(0,0,0,.06)}
.svc{position:absolute;display:flex;align-items:center;gap:14px;font-family:"Noto Sans",sans-serif;font-size:12px;line-height:13px;color:#333;letter-spacing:.2px}
.svc i{display:block;width:30px;height:28px;border-radius:5px;flex:none}
.svc-rule{position:absolute;height:1px;background:#dcdcdc}
.client{position:absolute;width:110px;text-align:center;font-family:"Ubuntu",sans-serif;font-weight:500;font-size:13px;color:var(--brown)}
.news{left:118px;top:1045px;width:811px;height:36px;background:var(--white);box-shadow:0 6px 8px -4px rgba(0,0,0,.25)}
.news .label{position:absolute;left:0;top:0;width:142px;height:36px;background:linear-gradient(#8c8c8c,#6f6f6f);color:var(--white);font-family:"Ubuntu",sans-serif;font-weight:500;font-size:13.5px;line-height:36px;padding-left:35px}
.news .feed{position:absolute;left:6px;top:8px;width:21px;height:21px;border-radius:4px;background:var(--gold)}
.news .text{position:absolute;left:152px;top:13px;font-size:9px;color:#222}
.news .play{position:absolute;left:784px;top:9px;width:18px;height:18px;border-radius:3px;border:1px solid var(--brown);background:#f2e6d6}
.footer{left:0;top:1104px;width:1046px;height:96px;background:var(--brown);border-top:3px solid #c9a273}
.footer .links{position:absolute;left:0;width:1046px;top:14px;text-align:center;font-size:11px;color:var(--white);word-spacing:2px}
.footer .links span{margin:0 11px}
.social{position:absolute;top:43px;width:24px;height:24px;border-radius:3px;background:#4a7fb8;border:1px solid #2d5a8c}
.footer .copy{position:absolute;left:0;width:1046px;top:77px;text-align:center;font-size:10.5px;color:#f6ebdc}
</style>
</head>
<body>
<header class="abs header">
  <div class="abs logo-art" role="img" aria-label="Golden company emblem with a figure holding a laptop"></div>
  <div class="abs logo-name">TADURK<br>INFORMATION<br>SYSTEMS PTE LTD</div>
  <nav class="abs top-links">
    <span>HOME</span><span class="sep">|</span><span>SITEMAP</span><span class="sep">|</span><span>LOG INCIDENT</span><span class="sep">|</span><span>ENQUIRY</span><span class="sep">|</span><span>CONTACT</span><span class="sep">|</span><span>CLIENT SUPPORT</span>
  </nav>
</header>

<nav class="abs main-nav">
  <span class="item active">COMPANY</span>
  <span class="item" style="left:367px">PRODUCTS</span>
  <span class="item" style="left:447px">LEDGRA</span>
  <span class="item" style="left:510px">SERVICES</span>
  <span class="item" style="left:584px">CLIENTELE</span>
  <span class="item" style="left:665px">CAREERS</span>
  <span class="item" style="left:738px">INFOBIN</span>
</nav>

<section class="hero">
  <div class="abs hero-art" role="img" aria-label="White figures fitting together coloured puzzle pieces"></div>
  <p class="abs hero-text">For more than 20 years, <em>LEDGRA</em> has provided reliable software solutions optimized to take advantage of new technologies and meet the unique requirements of companies.</p>
  <svg class="abs arrow" style="left:119px;top:282px" viewBox="0 0 27 27"><circle cx="13.5" cy="13.5" r="12" fill="none" stroke="#8f5c27" stroke-width="2"/><path d="M15.5 8 L10 13.5 L15.5 19" fill="none" stroke="#8f5c27" stroke-width="2"/></svg>
  <svg class="abs arrow" style="left:900px;top:282px" viewBox="0 0 27 27"><circle cx="13.5" cy="13.5" r="12" fill="none" stroke="#8f5c27" stroke-width="2"/><path d="M11.5 8 L17 13.5 L11.5 19" fill="none" stroke="#8f5c27" stroke-width="2"/></svg>
  <div class="dots"><span style="left:467px"></span><span style="left:505px"></span><span class="on" style="left:542px"></span></div>
</section>

<section class="abs card" style="left:153px">
  <h2>About Us</h2><div class="rule"></div>
  <p class="about">We have a large customer base, which spreads across Singapore, South East Asia and East Asia. This illustrates TIS is able to offer overseas support to customers who have regional operations.</p>
  <span class="btn" style="left:17px;top:150px">More</span>
</section>
<section class="abs card" style="left:398px">
  <h2>Testimonials</h2><div class="rule"></div>
  <span class="qmark">&ldquo;</span>
  <p class="quote">Lorem Ipsum is simply dummy text of the printing and typesetting industry. Lorem Ipsum is simply dummy text of the printing and typesetting industry.Lorem Ipsum has been...</p>
  <span class="by">- Daniel</span>
  <span class="btn" style="left:31px;top:150px">More</span>
</section>
<section class="abs card form" style="left:646px">
  <h2>Quick Contact</h2><div class="rule"></div>
  <label style="top:47px">Name:</label><span class="field" style="top:47px"></span>
  <label style="top:68px">Email:</label><span class="field" style="top:68px"></span>
  <label style="top:93px">Phone:</label><span class="field" style="top:92px"></span>
  <label style="top:115px">Message:</label><span class="field" style="top:115px;height:29px"></span>
  <span class="btn" style="left:66px;top:150px">Submit</span>
</section>
<div class="abs mascot" style="left:341px;top:450px" role="img" aria-label="Golden figure carrying a laptop"></div>
<div class="abs mascot" style="left:589px;top:450px" role="img" aria-label="Golden figure carrying a laptop"></div>
<div class="abs mascot" style="left:837px;top:450px" role="img" aria-label="Golden figure carrying a laptop"></div>

<section class="abs panel" style="left:153px;width:479px">
  <div class="svc" style="left:33px;top:40px"><i style="background:#b9c3cf"></i>Orvane Software and<br>Technology Reseller</div>
  <div class="svc" style="left:261px;top:37px"><i style="background:#4b4f5c;height:36px"></i>Ongoing Consultation</div>
  <div class="svc" style="left:33px;top:96px"><i style="background:#5fa2dc"></i>Consulting Services<br>for World</div>
  <div class="svc" style="left:262px;top:95px"><i style="background:#7fa6cc"></i>Project Management</div>
  <div class="svc" style="left:33px;top:143px"><i style="background:#c5b3c9"></i>Migrations &amp; Upgrades<br>to the 9's</div>
  <div class="svc" style="left:262px;top:141px"><i style="background:#b8cf9c"></i>Report Development</div>
  <div class="svc" style="left:33px;top:187px"><i style="background:#5f8fd1;height:20px"></i>Meridian One<br>Implementation Application</div>
  <div class="svc" style="left:262px;top:185px"><i style="background:#6e9f5e"></i>Hardware Certified</div>
  <div class="svc" style="left:33px;top:235px"><i style="background:#d6d1cc"></i>Technical and CNC</div>
  <div class="svc" style="left:262px;top:235px"><i style="background:#3b7fc7"></i>Software Integration</div>
  <div class="svc" style="left:33px;top:285px"><i style="background:#8b6b48"></i>Custom Applications<br>Development</div>
  <div class="svc" style="left:262px;top:283px"><i style="background:#4f7f4e"></i>BI Publisher for Halvor<br>Reporting Systems</div>
  <span class="svc-rule" style="left:263px;top:83px;width:200px"></span>
  <span class="svc-rule" style="left:263px;top:130px;width:200px"></span>
  <span class="svc-rule" style="left:263px;top:178px;width:200px"></span>
  <span class="svc-rule" style="left:263px;top:228px;width:200px"></span>
  <span class="svc-rule" style="left:263px;top:275px;width:200px"></span>
</section>
<div class="abs tab" style="left:162px;width:116px">Services</div>

<section class="abs panel" style="left:648px;width:233px">
  <div class="client" style="left:-7px;top:64px">Norhaven</div>
  <div class="client" style="left:121px;top:64px">Pellmore Dairy</div>
  <div class="client" style="left:-7px;top:117px">Quelby</div>
  <div class="client" style="left:121px;top:117px">Brackwell</div>
  <div class="client" style="left:-7px;top:168px">Lunora</div>
  <div class="client" style="left:121px;top:168px">Mervale</div>
  <div class="client" style="left:-7px;top:222px">Tressel Dairy</div>
  <div class="client" style="left:121px;top:222px">Aldrin</div>
  <div class="client" style="left:-7px;top:275px">Corbel</div>
  <div class="client" style="left:121px;top:275px">Sunmead</div>
</section>
<div class="abs tab" style="left:659px;width:115px">Clients</div>

<section class="abs news">
  <div class="label"><span class="feed"></span>LATEST NEWS</div>
  <p class="text">Lorem Ipsum is simply dummy text of the printing and typesetting industry.Duis aute irure dolor in reprehenderit in voluptate velit...</p>
  <svg class="play" viewBox="0 0 18 18"><path d="M7 5 L12 9 L7 13 Z" fill="#8f5c27"/></svg>
</section>

<footer class="abs footer">
  <div class="links"><span>Company</span>|<span>Products</span>|<span>LEDGRA</span>|<span>Services</span>|<span>Clientele</span>|<span>Careers</span>|<span>Infobin</span></div>
  <span class="social" style="left:480px" aria-label="Social link"></span>
  <span class="social" style="left:511px;background:#5cbde6" aria-label="Social link"></span>
  <span class="social" style="left:542px;background:#3f7eb5" aria-label="Social link"></span>
  <p class="copy">&copy; Copyrights 2013. Tadurk Information Systems. All Rights Reserved.</p>
</footer>
</body>
</html>
```